Business Card Design For Office Furniture Clearance Company

Kestrel Office Clearance - our company name pretty much explains what we do, we clear offices for high end clients, mainly plc's and large international companies.

We require a nice looking business card that displays professionalism but without being too serious.

It would be nice to see just a little more than a conventional boring business card, make sure you add some flare.

Industry/Entity Type

Office Furniture

Contact Information for Business Card

CARD 1

Mark Holloway
Director
mark@kestrelofficeclearance.co.uk
m: 07700 153928

t: 01632 960418
www.kestrelofficeclearance.co.uk

Kestrel Office Clearance
Unit K4 B
2-8 Fenwick Lane
Ashcombe
Northbrook Vale
ZZ9 4QT

free office clearances… you cant get better than that.

CARD 2

Peter Radford
Director
peter@kestrelofficeclearance.co.uk
m: 07700 382615

t: 01632 960418

Kestrel Office Clearance
Unit K4 B
2-8 Fenwick Lane
Ashcombe
Northbrook Vale
ZZ9 4QT

Font styles to use
Sans Serif

Requirements
Must have
• A white background - as we have a blue logo.
Nice to have
• Nice use of the logo - play around with this and dissect it.

```html
<!DOCTYPE html>
<html lang="en">
<head>
<meta charset="utf-8">
<title>Kestrel Office Clearance – Business Card</title>
<link rel="stylesheet" href="https://fonts.googleapis.com/css2?family=Lato:wght@400;700&display=swap">
<style>
  :root {
    --brand-blue: #0279bf;
    --white: #ffffff;
    --backdrop: #e7e4df;
    --shadow: rgba(0, 0, 0, 0.18);
  }
  * { margin: 0; padding: 0; box-sizing: border-box; }
  html, body {
    width: 1138px;
    height: 1200px;
    overflow: hidden;
    background: var(--backdrop);
    font-family: "Lato", Arial, sans-serif;
  }
  .canvas { position: relative; width: 1138px; height: 1200px; }
  .card {
    position: absolute;
    width: 670px;
    height: 382px;
    border-radius: 12px;
    overflow: hidden;
    box-shadow: 0 4px 12px var(--shadow);
    background: var(--brand-blue);
    color: var(--white);
  }
  .card--front { left: 218px; top: 198px; }
  .card--back { left: 216px; top: 618px; }

  .front__top-band {
    position: absolute; left: 0; top: 0;
    width: 100%; height: 146px;
    background: var(--white);
  }
  .front__badge {
    position: absolute;
    left: 36px; top: 48px;
    width: 292px; height: 292px;
    border-radius: 50%;
    background: var(--brand-blue);
    border: 3px solid var(--white);
    display: flex; align-items: center; justify-content: center;
  }
  .front__badge-name {
    font-weight: 700;
    font-size: 48px;
    color: var(--white);
  }
  .front__company {
    position: absolute;
    right: 36px; top: 58px;
    font-weight: 700;
    font-size: 31px;
    color: var(--brand-blue);
    white-space: nowrap;
  }
  .front__details {
    position: absolute;
    left: 358px; width: 300px;
    top: 148px;
    text-align: center;
  }
  .person__name { font-weight: 700; font-size: 24px; line-height: 30px; }
  .person__role { font-size: 16px; line-height: 18px; }
  .contact__icons {
    display: flex; justify-content: center; gap: 8px;
    margin-top: 20px; height: 18px;
  }
  .contact__icons svg { width: 16px; height: 16px; fill: none; stroke: var(--white); stroke-width: 1.8; }
  .contact__list { list-style: none; margin-top: 2px; font-size: 16px; line-height: 21.2px; white-space: nowrap; }

  .back__name {
    position: absolute; left: 0; right: 0; top: 166px;
    text-align: center;
    font-weight: 700; font-size: 40px;
  }
  .back__web {
    position: absolute; left: 0; right: 0; top: 340px;
    text-align: center; font-size: 15px;
  }
</style>
</head>
<body>
<main class="canvas">
  <section class="card card--front" aria-label="Business card front">
    <div class="front__top-band"></div>
    <div class="front__badge"><span class="front__badge-name">Kestrel</span></div>
    <h1 class="front__company">Kestrel Office Clearance</h1>
    <div class="front__details">
      <p class="person__name">Mark Holloway</p>
      <p class="person__role">Director</p>
      <div class="contact__icons" aria-hidden="true">
        <svg viewBox="0 0 16 16"><rect x="4.5" y="1.5" width="7" height="13" rx="1.2"/><line x1="7" y1="12.3" x2="9" y2="12.3"/></svg>
        <svg viewBox="0 0 16 16"><path d="M3 2.5l3 0 1 3.2-1.7 1.2a8 8 0 0 0 3.8 3.8l1.2-1.7 3.2 1v3c-6.5.3-10.8-4-10.5-10.5z"/></svg>
        <svg viewBox="0 0 16 16"><rect x="1.5" y="3.5" width="13" height="9"/><polyline points="1.5,3.5 8,9 14.5,3.5"/></svg>
        <svg viewBox="0 0 16 16"><circle cx="8" cy="8" r="6.5"/><ellipse cx="8" cy="8" rx="3" ry="6.5"/><line x1="1.5" y1="8" x2="14.5" y2="8"/><line x1="2.5" y1="4.8" x2="13.5" y2="4.8"/><line x1="2.5" y1="11.2" x2="13.5" y2="11.2"/></svg>
      </div>
      <ul class="contact__list">
        <li>07700 153928</li>
        <li>01632 960418</li>
        <li>mark@kestrelofficeclearance.co.uk</li>
        <li>www.kestrelofficeclearance.co.uk</li>
        <li>Unit K4 B 2-8 Fenwick Lane</li>
        <li>Ashcombe Northbrook Vale, ZZ9 4QT</li>
      </ul>
    </div>
  </section>

  <section class="card card--back" aria-label="Business card back">
    <p class="back__name">Kestrel</p>
    <p class="back__web">www.kestrelofficeclearance.co.uk</p>
  </section>
</main>
</body>
</html>
```